Dietitian needs awesome business card

I need a contemporary design that's eye catching but professional.
My card is to given to doctors, specialists and patients alike.
I manage patients with chronic diseases
I have uploaded my logo and current business card, I would also like the other Certified Clinical Nutritionist logo incorporated into the design

Target Market(s)

Doctors, specialists and patients

Industry/Entity Type

Healthcare

Contact Information for Business Card

www.brightfieldnutrition.com.au
Ph: 0427 561 903
Fax: 6457 2183
email: marcus.k.diet@fernmail.com
Space on the back of the card with: Appointment date, Appointment time and appointment location

Font styles to use
Serif

Colors
fbee3e
876aae
ffc214

Requirements
Must have
• My Logo
• Certified Clinical Nutritionist Logo
• My 4 locations - Pinebrook Medical Centre, North Corrin Health, Hollis Medical, Ashcombe Doctors Surgery
Nice to have
• I like the colours in my current business card

```html
<!DOCTYPE html>
<html lang="en">
<head>
<meta charset="utf-8">
<title>Brightfield Nutrition &amp; Dietetics – Business Card</title>
<link rel="stylesheet" href="https://fonts.googleapis.com/css2?family=Arimo:wght@400;700&display=swap">
<style>
  :root {
    --stage: #e9eaec;
    --card: #ffffff;
    --navy: #1b2585;
    --blue-mid: #0a8ac8;
    --orange: #f07b1d;
    --green: #78b928;
    --lime: #c4e00e;
    --text: #4a4a4a;
    --rule: #c9ccd0;
    --divider: #d4d4d4;
  }
  * { box-sizing: border-box; margin: 0; padding: 0; }
  html, body { width: 1200px; height: 987px; overflow: hidden; }
  body {
    background: var(--stage);
    font-family: "Arimo", Arial, sans-serif;
    color: var(--text);
    position: relative;
  }
  .card {
    position: absolute;
    left: 293px;
    width: 615px;
    height: 351px;
    background: var(--card);
    border-radius: 19px;
    overflow: hidden;
    box-shadow: 0 4px 14px rgba(0,0,0,.18);
  }
  .card--front { top: 128px; }
  .card--back { top: 507px; }

  /* front */
  .brand {
    position: absolute;
    left: 36px; top: 286px;
    top: 158px;
    display: flex; align-items: center; gap: 10px;
  }
  .brand__dot {
    width: 38px; height: 38px; border-radius: 50%;
    background: var(--navy);
    flex: none;
  }
  .brand__name {
    font-size: 17px; line-height: 1.25; color: var(--navy); font-weight: 400;
    width: 180px;
  }
  .divider {
    position: absolute; left: 289px; top: 86px;
    width: 1px; height: 179px; background: var(--divider);
  }
  .person { position: absolute; left: 313px; top: 86px; }
  .person__name { font-size: 22px; font-weight: 700; color: var(--navy); line-height: 1.2; }
  .person__role { font-size: 16px; line-height: 22px; }
  .person__role--primary { color: var(--orange); margin-top: 3px; }
  .person__role--secondary { color: var(--green); }
  .contacts { list-style: none; margin-top: 10px; }
  .contacts li {
    display: flex; align-items: center; gap: 10px;
    font-size: 16px; line-height: 23.5px; color: var(--text);
  }
  .contacts svg { width: 16px; height: 16px; fill: var(--navy); flex: none; }
  .band { position: absolute; left: 0; bottom: 0; width: 615px; height: 24px; }

  /* back */
  .back-photo {
    position: absolute; inset: 0;
    background: radial-gradient(ellipse at 60% 55%, #eef2e6 0%, #f7f8f4 45%, #fbfbfa 100%);
  }
  .appointment { position: absolute; inset: 0; }
  .appointment__title {
    position: absolute; top: 30px; left: 0; width: 100%;
    text-align: center; font-size: 20px; font-weight: 700; color: var(--navy);
  }
  .appointment__line {
    position: absolute; left: 42px; width: 530px; height: 1px; background: var(--rule);
  }
  .when {
    position: absolute; left: 42px; top: 221px; width: 530px;
    font-size: 16px; color: var(--navy); white-space: nowrap;
  }
  .when__dots { color: var(--navy); letter-spacing: 0.5px; }
  .when__ampm { font-size: 12px; }
  .locations {
    position: absolute; left: 42px; top: 266px; width: 540px;
    list-style: none; display: grid; grid-template-columns: 306px 1fr; row-gap: 5px;
  }
  .locations li { display: flex; align-items: center; gap: 6px; font-size: 16px; line-height: 18px; color: var(--text); }
  .locations .box { width: 13px; height: 13px; border: 1.5px solid var(--navy); flex: none; }
</style>
</head>
<body>

<section class="card card--front">
  <div class="brand">
    <span class="brand__dot"></span>
    <span class="brand__name">Brightfield Nutrition &amp; Dietetics</span>
  </div>

  <div class="divider"></div>

  <div class="person">
    <p class="person__name">Marcus Kellan</p>
    <p class="person__role person__role--primary">Certified Clinical Nutritionist</p>
    <p class="person__role person__role--secondary">Nutritionist &amp; Chef</p>
    <ul class="contacts">
      <li><svg viewBox="0 0 16 16"><path d="M3.5 1.5l2.6 2.6-1.4 2a9 9 0 0 0 5.2 5.2l2-1.4 2.6 2.6-1.9 2C7.2 14 2 8.8 1.5 3.4z"/></svg>0427 561 903</li>
      <li><svg viewBox="0 0 16 16"><path d="M4 1h8v4H4zM1 6h14v7h-3v2H4v-2H1zm4 5v3h6v-3z"/></svg>6457 2183</li>
      <li><svg viewBox="0 0 16 16"><path d="M1 3h14v10H1zm1.5 1.4V5l5.5 4 5.5-4v-.6L8 8.2z"/></svg>marcus.k.diet@fernmail.com</li>
      <li><svg viewBox="0 0 16 16"><path d="M8 1a7 7 0 1 0 0 14A7 7 0 0 0 8 1zm-2 3.5l2 1.5-.5 2 2 1-.5 3-2-1.5-1-2.5-1.5-.5z"/></svg>brightfieldnutrition.com.au</li>
    </ul>
  </div>

  <svg class="band" viewBox="0 0 615 24" preserveAspectRatio="none" aria-hidden="true">
    <defs>
      <linearGradient id="band-blue" x1="0" x2="1">
        <stop offset="0" stop-color="#1b2585"/>
        <stop offset="0.55" stop-color="#0a8ac8"/>
        <stop offset="1" stop-color="#1b2585"/>
      </linearGradient>
      <linearGradient id="band-green" x1="0" x2="1">
        <stop offset="0" stop-color="#1c9a3a"/>
        <stop offset="1" stop-color="#c4e00e"/>
      </linearGradient>
    </defs>
    <polygon points="0,0 400,0 393,24 0,24" fill="url(#band-blue)"/>
    <polygon points="405,0 615,0 615,24 398,24" fill="url(#band-green)"/>
  </svg>
</section>

<section class="card card--back">
  <div class="back-photo" role="img" aria-label="Faint background photograph of fresh green vegetables and herbs"></div>
  <div class="appointment">
    <h2 class="appointment__title">YOUR APPOINTMENT</h2>
    <div class="appointment__line" style="top:84px"></div>
    <div class="appointment__line" style="top:119px"></div>
    <div class="appointment__line" style="top:154px"></div>
    <div class="appointment__line" style="top:189px"></div>
    <p class="when">Date :&nbsp;&nbsp;<span class="when__dots">..............................................</span>&nbsp;Time :&nbsp;<span class="when__dots">...............................</span>&nbsp;<span class="when__ampm">AM/PM</span></p>
    <ul class="locations">
      <li><span class="box"></span>Pinebrook Medical Centre</li>
      <li><span class="box"></span>Hollis Medical</li>
      <li><span class="box"></span>North Corrin Health</li>
      <li><span class="box"></span>Ashcombe Doctors Surgery</li>
    </ul>
  </div>
</section>

</body>
</html>
```